Business Card Design Project - 2 sided

We need a business card design for a card having one business on each side (ie. two businesses on one card). Would like a design that incorporates logo, tagline and normal fields (name, position, address, phone).

Would also like an allowance for small font text along the bottom (text to be determined, but less than 50 characters).

NB. Attached logo for Harbor Quill has two variations - either can be used.

www.harborquill-example.com / www.velmaro-example.com

```html
<!DOCTYPE html>
<html lang="en">
<head>
<meta charset="utf-8">
<title>Harbor Quill / Velmaro Business Card</title>
<link href="https://fonts.googleapis.com/css2?family=Open+Sans:wght@400;600;700&display=swap" rel="stylesheet">
<style>
  :root {
    --backdrop: #e9e6e2;
    --card: #ffffff;
    --green: #8cc43f;
    --green-dark: #7ab232;
    --swoosh: #6d6e71;
    --navy: #2b2d6e;
    --blue: #2a86c8;
    --ink: #555555;
    --white: #ffffff;
  }
  * { box-sizing: border-box; margin: 0; padding: 0; }
  html, body { width: 1200px; height: 487px; overflow: hidden; }
  body {
    background: var(--backdrop);
    font-family: "Open Sans", Arial, sans-serif;
    position: relative;
  }
  .card {
    position: absolute;
    top: 88px;
    width: 545px;
    height: 312px;
    background: var(--card);
    border-radius: 14px;
    overflow: hidden;
    box-shadow: 0 2px 8px rgba(0,0,0,.25);
  }
  .card--front { left: 41px; }
  .card--back { left: 614px; }
  .card__band { position: absolute; left: 0; top: 0; width: 545px; height: 312px; }
  .brand {
    position: absolute; left: 0; right: 0; top: 42px;
    display: flex; flex-direction: column; align-items: center;
  }
  .brand__row { display: flex; align-items: center; gap: 12px; height: 90px; }
  .brand__dot { width: 26px; height: 26px; border-radius: 50%; background: var(--green); }
  .brand__name { font-weight: 600; font-size: 34px; letter-spacing: 1px; }
  .card--front .brand__name { color: var(--navy); }
  .card--back .brand__name { color: var(--blue); }
  .brand__tagline { font-size: 11.5px; color: var(--ink); margin-top: 4px; }
  .card--front .brand__tagline { color: #444; font-weight: 600; }
  .card--back .brand__tagline { font-size: 14px; color: #444; margin-top: 0; }
  .holder {
    position: absolute; left: 0; right: 0; top: 158px;
    text-align: center; font-size: 13px; color: var(--ink);
  }
  .holder__name { color: var(--green); font-weight: 700; font-size: 17px; }
  .contacts {
    position: absolute; left: 50px; right: 30px; top: 220px;
    display: flex; color: var(--white); font-size: 13.5px; line-height: 19px;
  }
  .contacts__group { padding: 0 9px; }
  .contacts__group + .contacts__group { border-left: 1px solid rgba(255,255,255,.55); }
  .contacts__item { display: flex; align-items: center; gap: 6px; }
  .contacts__item svg { width: 11px; height: 11px; fill: var(--white); flex: none; }
  .fineprint {
    position: absolute; left: 0; right: 0; top: 264px;
    text-align: center; color: var(--white); font-size: 11px; letter-spacing: .2px;
  }
</style>
</head>
<body>

<section class="card card--front">
  <svg class="card__band" viewBox="0 0 545 312" aria-hidden="true">
    <path d="M0 170 C150 178 330 185 545 213 L545 222 C330 196 150 192 0 196 Z" fill="var(--swoosh)"/>
    <path d="M0 196 C150 192 330 197 545 222 L545 312 L0 312 Z" fill="var(--green)"/>
  </svg>
  <div class="brand">
    <div class="brand__row">
      <span class="brand__dot"></span>
      <span class="brand__name">Harbor Quill</span>
    </div>
    <p class="brand__tagline">Website Translation and Localisation Specialist...</p>
  </div>
  <p class="holder"><span class="holder__name">YOUR NAME</span> / Title</p>
  <div class="contacts">
    <div class="contacts__group">
      <p class="contacts__item"><svg viewBox="0 0 12 12"><path d="M2 1h3l1 3-1.5 1a7 7 0 0 0 2.5 2.5L8 6l3 1v3a1 1 0 0 1-1 1A9 9 0 0 1 1 2a1 1 0 0 1 1-1z"/></svg>123-456-7890</p>
      <p class="contacts__item"><svg viewBox="0 0 12 12"><rect x="3" y="0" width="6" height="12" rx="1"/></svg>123-456-7890</p>
    </div>
    <div class="contacts__group">
      <p class="contacts__item"><svg viewBox="0 0 12 12"><path d="M0 2h12v8H0z M0 2l6 4 6-4" stroke="var(--green)" stroke-width="1"/></svg>name@website.com</p>
      <p class="contacts__item"><svg viewBox="0 0 12 12"><circle cx="6" cy="6" r="6"/></svg>www.website.com</p>
    </div>
    <div class="contacts__group">
      <p>Complex name, Street</p>
      <p>City, State, zip code</p>
    </div>
  </div>
  <p class="fineprint">xxxxxxxxxxxxxxxxxxxxxxxxxxxxxxxxxxxxxxxxxxxxxxxxxx</p>
</section>

<section class="card card--back">
  <svg class="card__band" viewBox="0 0 545 312" aria-hidden="true">
    <path d="M0 170 C150 178 330 185 545 213 L545 222 C330 196 150 192 0 196 Z" fill="var(--swoosh)"/>
    <path d="M0 196 C150 192 330 197 545 222 L545 312 L0 312 Z" fill="var(--green)"/>
  </svg>
  <div class="brand">
    <div class="brand__row">
      <span class="brand__dot"></span>
      <span class="brand__name">Velmaro</span>
    </div>
    <p class="brand__tagline">Professional SEO Services</p>
  </div>
  <p class="holder"><span class="holder__name">YOUR NAME</span> / Title</p>
  <div class="contacts">
    <div class="contacts__group">
      <p class="contacts__item"><svg viewBox="0 0 12 12"><path d="M2 1h3l1 3-1.5 1a7 7 0 0 0 2.5 2.5L8 6l3 1v3a1 1 0 0 1-1 1A9 9 0 0 1 1 2a1 1 0 0 1 1-1z"/></svg>123-456-7890</p>
      <p class="contacts__item"><svg viewBox="0 0 12 12"><rect x="3" y="0" width="6" height="12" rx="1"/></svg>123-456-7890</p>
    </div>
    <div class="contacts__group">
      <p class="contacts__item"><svg viewBox="0 0 12 12"><path d="M0 2h12v8H0z M0 2l6 4 6-4" stroke="var(--green)" stroke-width="1"/></svg>name@website.com</p>
      <p class="contacts__item"><svg viewBox="0 0 12 12"><circle cx="6" cy="6" r="6"/></svg>www.website.com</p>
    </div>
    <div class="contacts__group">
      <p>Complex name, Street</p>
      <p>City, State, zip code</p>
    </div>
  </div>
  <p class="fineprint">xxxxxxxxxxxxxxxxxxxxxxxxxxxxxxxxxxxxxxxxxxxxxxxxxx</p>
</section>

</body>
</html>
```